Business Card Design

I already have a company logo for my company. I have a logo for the manufacturer we represent. I want a professional business card design.

```html
<!DOCTYPE html>
<html lang="en">
<head>
<meta charset="utf-8">
<title>Signal Guard LLC – Business Card</title>
<link rel="stylesheet" href="https://fonts.googleapis.com/css2?family=Open+Sans:wght@400;600;700&display=swap">
<style>
  :root {
    --page-bg: #d9d3cb;
    --card-light: #ece7e0;
    --card-dark: #1d1b1b;
    --accent-red: #c8151b;
    --accent-gold: #d29a22;
    --divider-cream: #efe6d6;
    --text-light: #e6e1da;
    --text-logo: #4a4a4a;
  }
  html, body {
    margin: 0;
    width: 1200px;
    height: 1047px;
    overflow: hidden;
    background: var(--page-bg);
  }
  .business-card {
    position: absolute;
    left: 80px;
    top: 240px;
    width: 1040px;
    height: 567px;
    border-radius: 26px;
    overflow: hidden;
    background: var(--card-light);
    box-shadow: 0 10px 30px rgba(0,0,0,0.18);
  }
  .business-card svg { display: block; width: 100%; height: 100%; }
  .card-text { font-family: "Open Sans", sans-serif; }
  .brand-name { font-weight: 700; fill: var(--text-logo); font-size: 30px; letter-spacing: 1px; }
  .holder-name { font-weight: 700; fill: var(--accent-red); font-size: 27px; }
  .holder-role, .contact-line { font-weight: 400; fill: var(--text-light); font-size: 21px; }
  .icon { fill: var(--accent-red); }
</style>
</head>
<body>
  <div class="business-card">
    <svg viewBox="0 0 880 480" preserveAspectRatio="none" class="card-text">
      <!-- gold band -->
      <path fill="var(--accent-gold)" d="M0,362 C250,352 380,232 500,152 C620,74 760,54 880,46 L880,94 C760,100 620,120 500,198 C380,278 250,400 0,410 Z"/>
      <!-- cream divider between gold band and dark field -->
      <path fill="none" stroke="var(--divider-cream)" stroke-width="5" d="M0,409 C250,398 380,278 500,198 C620,120 760,100 880,94"/>
      <!-- dark field -->
      <path fill="var(--card-dark)" d="M0,412 C250,401 380,281 500,201 C620,123 760,103 880,97 L880,480 L0,480 Z"/>
      <!-- red sweep -->
      <path fill="var(--accent-red)" d="M0,322 C230,318 370,200 490,120 C600,50 760,36 860,40 C760,48 620,70 510,140 C380,226 250,356 0,360 Z"/>

      <!-- brand -->
      <rect class="icon" x="38" y="150" width="26" height="26"/>
      <text class="brand-name" x="76" y="174">SIGNAL GUARD LLC</text>

      <!-- holder -->
      <rect fill="var(--accent-red)" x="863" y="197" width="17" height="57"/>
      <text class="holder-name" x="848" y="219" text-anchor="end">DANIEL CARTER</text>
      <text class="holder-role" x="848" y="250" text-anchor="end">Managing Director</text>

      <!-- address -->
      <text class="contact-line" x="848" y="298" text-anchor="end">Your address, City</text>
      <text class="contact-line" x="848" y="329" text-anchor="end">State, Zip 1234</text>

      <!-- contacts -->
      <text class="contact-line" x="817" y="380" text-anchor="end">123 456 789</text>
      <text class="contact-line" x="817" y="410" text-anchor="end">info@yourmail.com</text>
      <text class="contact-line" x="817" y="440" text-anchor="end">www.yourwebsite.com</text>

      <!-- phone icon -->
      <path class="icon" d="M831,366 l4,0 l2,5 l-2,2 a10,10 0 0 0 5,5 l2,-2 l5,2 l0,4 a3,3 0 0 1 -3,2 a17,17 0 0 1 -15,-15 a3,3 0 0 1 2,-3 Z"/>
      <!-- mail icon -->
      <rect class="icon" x="830" y="397" width="17" height="12" rx="1"/>
      <path d="M830,398 l8.5,6 l8.5,-6" fill="none" stroke="var(--card-dark)" stroke-width="1.5"/>
      <!-- globe icon -->
      <circle class="icon" cx="838.5" cy="433" r="8.5"/>
      <path d="M830,433 h17 M838.5,424.5 v17 M833,428 q5.5,3 11,0 M833,438 q5.5,-3 11,0" fill="none" stroke="var(--card-dark)" stroke-width="1.2"/>
    </svg>
  </div>
</body>
</html>
```